Website for designing and selling name-labels

We are looking for a fresh design for a site similar to these (www.tovskrabe.no, www.dremsgard.no, www.kvalbuffo.no) where the consumer can come online designing their own labels (30x15 mm) , either with onlye text or with text, choose a pre-defined symbol (which we have) and/or a color. We will the print the labels on our side, and send it to the customer.

We are looking for the front page, product page and check out - page.

Target Market(s)

families with childring, scools, kinder garden, industry

Number of Pages Required

3 page

Requirements
Nice to have
• bright and easy design
easy to design and see their own designs
easy check out - few steps

```html
<!DOCTYPE html>
<html lang="en">
<head>
<meta charset="utf-8">
<title>Lappelund.no – Name tags</title>
<link rel="stylesheet" href="https://fonts.googleapis.com/css2?family=Poppins:wght@500;600;700;800&family=Lato:wght@400;700&display=swap">
<style>
:root{
  --teal:#1f8f80;
  --ink:#111;
  --text:#333;
  --grey-band:#f4f0f0;
  --footer:#2a2a2a;
  --footer-text:#d8d8d8;
  --star:#f5a623;
  --white:#fff;
}
*{box-sizing:border-box;margin:0;padding:0}
html,body{width:1200px;height:2490px;overflow:hidden}
body{position:relative;background:var(--white);font-family:'Lato',sans-serif;color:var(--text)}
.abs{position:absolute}
.heading{font-family:'Poppins',sans-serif;font-weight:800;color:var(--ink);text-transform:uppercase;line-height:1.2}

/* header */
.logo{position:absolute;left:132px;top:27px;width:204px;height:56px;background:var(--teal);border-radius:8px;display:flex;align-items:center;justify-content:center;font-family:'Poppins',sans-serif;font-weight:800;color:var(--white);font-size:17px;letter-spacing:.5px}
.search{left:741px;top:21px;width:210px;height:31px;border:1px solid #999;font-family:'Poppins',sans-serif;font-size:11px;color:#333;padding:8px 14px}
.search svg{position:absolute;right:9px;top:8px}
.cart{left:974px;top:22px;display:flex;align-items:center;gap:4px;font-family:'Poppins',sans-serif;font-size:11px;font-weight:600;color:#222}
.cart-badge{position:absolute;right:-2px;top:-2px;width:16px;height:16px;border-radius:50%;background:var(--teal);color:#fff;font-size:10px;text-align:center;line-height:16px}
.nav{left:366px;top:71px;display:flex;gap:27px;font-family:'Poppins',sans-serif;font-weight:500;font-size:13.5px;color:#111}

/* hero */
.hero{left:0;top:101px;width:1200px;height:588px;background:
  radial-gradient(ellipse 220px 160px at 860px 290px,rgba(10,12,18,.75),rgba(10,12,18,0) 100%),
  radial-gradient(ellipse 60px 60px at 490px 320px,rgba(230,220,200,.55),rgba(230,220,200,0)),
  radial-gradient(ellipse 420px 300px at 980px 200px,#5a7ba8 0%,rgba(90,123,168,0) 100%),
  radial-gradient(ellipse 260px 200px at 470px 560px,rgba(170,110,50,.45),rgba(170,110,50,0)),
  radial-gradient(ellipse 500px 350px at 300px 150px,#34517e 0%,rgba(52,81,126,0) 100%),
  linear-gradient(120deg,#1a2a46 0%,#29436b 45%,#1c2e4d 75%,#0e1626 100%)}
.hero-title{left:131px;top:316px;font-size:46px;line-height:1.2;letter-spacing:.5px;color:var(--white)}
.btn{display:inline-flex;align-items:center;justify-content:center;font-family:'Poppins',sans-serif;font-weight:700;text-transform:uppercase;border-radius:4px}
.btn-teal{background:var(--teal);color:var(--white)}
.btn-white{background:var(--white);color:var(--ink)}
.hero-btn{left:135px;top:504px;width:153px;height:53px;font-size:17px}
.dots{left:562px;top:642px;display:flex;gap:11px}
.dots span{width:7px;height:7px;border-radius:50%;background:var(--white)}
.dots span.on{background:var(--teal)}

/* category cards */
.card{position:absolute;width:458px;height:335px;border-radius:4px;overflow:hidden}
.card-photo{position:absolute;inset:0}
.card h2{font-size:27px;line-height:1.22}
.card p{font-size:14.5px;line-height:1.22;color:#222}
.card .btn{width:94px;height:32px;font-size:11px}
.on-dark h2,.on-dark p{color:var(--white)}

/* reviews */
.reviews{left:0;top:1456px;width:1200px;height:352px;background:var(--grey-band)}
.reviews-title{left:131px;top:1488px;font-size:27px}
.arrows{left:1026px;top:1499px;display:flex;gap:10px}
.review{position:absolute;top:1543px;width:298px;height:220px;background:var(--white);border-radius:6px;padding:22px 31px}
.stars{color:var(--star);font-size:15px;letter-spacing:1px}
.review h3{font-family:'Poppins',sans-serif;font-weight:700;font-size:16px;color:var(--ink);margin:4px 0 9px}
.review p{font-size:14px;line-height:17.6px;color:#333;width:226px}
.review .author{font-size:12.5px;margin-top:16px;color:#222}

/* name tags */
.tags-title{left:0;width:1200px;top:1853px;text-align:center;font-size:27px}
.tile{position:absolute;top:1920px;width:180px;height:180px}

/* footer */
.footer{left:0;top:2149px;width:1200px;height:341px;background:var(--footer)}
.footer-logo{left:132px;top:2236px;width:279px;height:77px;background:var(--teal);border-radius:8px;display:flex;align-items:center;justify-content:center;font-family:'Poppins',sans-serif;font-weight:800;color:var(--white);font-size:22px;letter-spacing:.5px}
.foot-h{font-family:'Poppins',sans-serif;font-weight:600;font-size:13px;color:var(--white);top:2187px}
.foot-menu{left:492px;top:2226px;font-size:12.5px;line-height:19.6px;color:var(--footer-text)}
.foot-item{position:absolute;display:flex;align-items:flex-start;gap:9px;font-size:12px;line-height:16px;color:var(--footer-text)}
.foot-icon{width:24px;height:24px;border-radius:50%;background:var(--white);flex:none;display:flex;align-items:center;justify-content:center}
.divider{left:132px;top:2408px;width:932px;height:1px;background:#4a4a4a}
.copy{left:0;width:1200px;top:2449px;text-align:center;font-size:10px;color:var(--footer-text)}
</style>
</head>
<body>

<!-- header -->
<div class="logo">LAPPELUND.NO</div>
<div class="abs search">SEARCH
  <svg width="12" height="12" viewBox="0 0 12 12"><circle cx="5" cy="5" r="3.8" fill="none" stroke="#777" stroke-width="1.4"/><line x1="8" y1="8" x2="11" y2="11" stroke="#777" stroke-width="1.5"/></svg>
</div>
<div class="abs cart">MY CART
  <svg width="34" height="30" viewBox="0 0 34 30"><path d="M1 4h5l4 16h16l3-11H8" fill="none" stroke="#333" stroke-width="1.6"/><line x1="11" y1="13" x2="28" y2="13" stroke="#333" stroke-width="1.2"/><line x1="16" y1="9" x2="16" y2="20" stroke="#333" stroke-width="1.2"/><line x1="22" y1="9" x2="22" y2="20" stroke="#333" stroke-width="1.2"/><circle cx="12" cy="25" r="2" fill="#333"/><circle cx="24" cy="25" r="2" fill="#333"/></svg>
  <span class="cart-badge">0</span>
</div>
<nav class="abs nav"><span>NAME TAGS</span><span>MINILAPPER</span><span style="margin-left:7px">IRONING PADS</span><span>TEMALAPPER</span><span>DRINKING BOTTLE</span><span style="margin-left:-6px">CONTACT US</span></nav>

<!-- hero -->
<div class="abs hero" role="img" aria-label="Close-up of a denim jacket with a sewn-in black name label"></div>
<h1 class="abs heading hero-title">Design your<br>own name<br>tags</h1>
<div class="abs btn btn-teal hero-btn">Shop now</div>
<div class="abs dots"><span></span><span></span><span class="on"></span><span></span><span></span></div>

<!-- category cards -->
<div class="card" style="left:132px;top:718px;border:1px solid #bbb;background:#f4f1f1">
  <div class="card-photo" role="img" aria-label="Four colourful highlighter pens with name labels" style="background:
    radial-gradient(ellipse 40px 80px at 215px 170px,rgba(240,40,100,.55),rgba(240,40,100,0)),
    radial-gradient(ellipse 80px 50px at 340px 90px,rgba(70,150,220,.5),rgba(70,150,220,0)),
    radial-gradient(ellipse 40px 80px at 445px 210px,rgba(40,200,80,.5),rgba(40,200,80,0)),
    radial-gradient(ellipse 80px 50px at 290px 290px,rgba(200,240,60,.55),rgba(200,240,60,0)),
    #f4f1f1"></div>
  <div class="abs" style="left:33px;top:52px;width:150px">
    <h2 class="heading">Multi-<br>colored<br>pencil</h2>
    <p style="width:135px;margin:14px 0 24px">Lorem Ipsum is simply dummy text of the printing</p>
    <div class="btn btn-teal">Shop now</div>
  </div>
</div>

<div class="card" style="left:608px;top:718px">
  <div class="card-photo" role="img" aria-label="Person holding a navy handbag with a name label" style="background:
    radial-gradient(ellipse 110px 110px at 300px 200px,#1b2238 0%,rgba(27,34,56,.85) 55%,rgba(27,34,56,0) 100%),
    radial-gradient(ellipse 90px 120px at 340px 60px,rgba(130,160,210,.8),rgba(130,160,210,0)),
    radial-gradient(ellipse 60px 200px at 200px 170px,rgba(200,160,120,.8),rgba(200,160,120,0)),
    radial-gradient(ellipse 90px 120px at 430px 290px,rgba(60,80,120,.8),rgba(60,80,120,0)),
    linear-gradient(90deg,#c8c8cc 0%,#bdbbc0 36%,#a9a7ac 38%,#c6b6a4 50%,#8d9bbd 75%,#4d5f86 100%)"></div>
  <div class="abs" style="left:33px;top:66px;width:140px">
    <h2 class="heading">Hand<br>bag</h2>
    <p style="width:135px;margin:14px 0 20px">Lorem Ipsum is simply dummy text of the printing</p>
    <div class="btn btn-teal">Shop now</div>
  </div>
</div>

<div class="card on-dark" style="left:132px;top:1077px">
  <div class="card-photo" role="img" aria-label="Travel bag with a yellow luggage tag on blue wooden boards" style="background:
    radial-gradient(ellipse 100px 45px at 220px 190px,rgba(245,170,20,.85),rgba(245,170,20,0)),
    radial-gradient(ellipse 90px 50px at 270px 270px,rgba(230,220,230,.55),rgba(230,220,230,0)),
    radial-gradient(ellipse 170px 200px at 440px 140px,#3a3d42 0%,rgba(58,61,66,.7) 55%,rgba(58,61,66,0) 100%),
    linear-gradient(180deg,#2ea3d8 0%,#1f93cc 50%,#2c9ad2 100%)"></div>
  <div class="abs" style="left:33px;top:42px;width:230px">
    <h2 class="heading">Travel bag</h2>
    <p style="color:#111;margin:2px 0 14px">Lorem Ipsum is simply dummy text of the printing</p>
    <div class="btn btn-white">Shop now</div>
  </div>
</div>

<div class="card on-dark" style="left:606px;top:1077px">
  <div class="card-photo" role="img" aria-label="Grey sweater collar with a sewn name label" style="background:
    radial-gradient(ellipse 55px 90px at 280px 150px,rgba(225,222,205,.95),rgba(225,222,205,0)),
    radial-gradient(ellipse 200px 30px at 340px 250px,rgba(150,100,60,.75),rgba(150,100,60,0)),
    radial-gradient(ellipse 260px 150px at 200px 40px,rgba(160,165,180,.8),rgba(160,165,180,0)),
    linear-gradient(135deg,#8f93a3 0%,#7a7f90 50%,#575b6b 100%)"></div>
  <div class="abs" style="left:34px;top:190px;width:230px">
    <h2 class="heading">T shirt</h2>
    <p style="margin:2px 0 14px">Lorem Ipsum is simply dummy text of the printing</p>
    <div class="btn btn-white">Shop now</div>
  </div>
</div>

<!-- reviews -->
<div class="abs reviews"></div>
<h2 class="abs heading reviews-title">Reviews</h2>
<div class="abs arrows">
  <svg width="14" height="22" viewBox="0 0 14 22"><path d="M11 2L3 11l8 9" fill="none" stroke="#999" stroke-width="2"/></svg>
  <svg width="14" height="22" viewBox="0 0 14 22"><path d="M3 2l8 9-8 9" fill="none" stroke="#999" stroke-width="2"/></svg>
</div>
<div class="review" style="left:132px"><div class="stars">★★★★★</div><h3>Very happy!</h3><p>There are many variations of passages of Lorem Ipsum avail able, but the majority have suffe red alteration in some form, by injected humour.</p><div class="author">Ingrid</div></div>
<div class="review" style="left:453px"><div class="stars">★★★★★</div><h3>Very happy!</h3><p>There are many variations of passages of Lorem Ipsum avail able, but the majority have suffe red alteration in some form, by injected humour.</p><div class="author">Ingrid</div></div>
<div class="review" style="left:769px"><div class="stars">★★★★★</div><h3>Very happy!</h3><p>There are many variations of passages of Lorem Ipsum avail able, but the majority have suffe red alteration in some form, by injected humour.</p><div class="author">Ingrid</div></div>

<!-- name tags -->
<h2 class="abs heading tags-title">Name tags</h2>
<div class="tile" style="left:132px;background:radial-gradient(ellipse 60px 40px at 70px 80px,rgba(230,130,110,.45),rgba(230,130,110,0)),radial-gradient(ellipse 50px 40px at 120px 50px,rgba(200,90,60,.4),rgba(200,90,60,0)),linear-gradient(180deg,#bfe0f2 0%,#e4f1f9 55%,#f6f9fc 100%)" role="img" aria-label="Cartoon of two children waving"></div>
<div class="tile" style="left:322px;background:radial-gradient(ellipse 45px 70px at 115px 110px,rgba(250,250,250,.8),rgba(250,250,250,0)),radial-gradient(ellipse 20px 80px at 35px 110px,rgba(230,130,50,.65),rgba(230,130,50,0)),linear-gradient(180deg,#b3cbdc,#97b1c5)" role="img" aria-label="Cartoon businessman with brand letter blocks"></div>
<div class="tile" style="left:510px;background:radial-gradient(ellipse 45px 60px at 75px 110px,rgba(245,150,30,.75),rgba(245,150,30,0)),radial-gradient(ellipse 30px 25px at 140px 55px,rgba(90,200,200,.6),rgba(90,200,200,0)),radial-gradient(circle,#b3202a,#6e0f16)" role="img" aria-label="Cartoon carrot character with glasses"></div>
<div class="tile" style="left:697px;background:radial-gradient(ellipse 70px 80px at 90px 105px,#2d6fc8 0%,rgba(45,111,200,.6) 60%,rgba(45,111,200,0) 100%),linear-gradient(180deg,#c9d4ea,#aab9dc)" role="img" aria-label="Cartoon blue monster with glasses"></div>
<div class="tile" style="left:885px;background:radial-gradient(ellipse 30px 70px at 90px 100px,rgba(190,110,200,.6),rgba(190,110,200,0)),radial-gradient(ellipse 30px 25px at 90px 35px,rgba(240,120,60,.6),rgba(240,120,60,0)),linear-gradient(180deg,#3aa3d9,#13679f)" role="img" aria-label="Cartoon mermaid underwater"></div>

<!-- footer -->
<div class="abs footer"></div>
<div class="abs footer-logo">LAPPELUND.NO</div>

<div class="abs foot-h" style="left:492px">MENU</div>
<div class="abs foot-menu">NAME TAGS<br>MINILAPPER<br>IRONING PADS<br>TEMALAPPER<br>DRINKING BOTTLE<br>CONTACT US</div>

<div class="abs foot-h" style="left:696px">CONTACT US</div>
<div class="foot-item" style="left:694px;top:2227px"><span class="foot-icon"><svg width="10" height="12" viewBox="0 0 10 12"><path d="M5 11S1 6.5 1 4a4 4 0 018 0c0 2.5-4 7-4 7z" fill="#333"/><circle cx="5" cy="4" r="1.4" fill="#fff"/></svg></span><span>22 Fjellveien<br>0575 Oslo</span></div>
<div class="foot-item" style="left:694px;top:2279px"><span class="foot-icon"><svg width="11" height="11" viewBox="0 0 11 11"><path d="M2 1l2 2-1 1.5c.8 1.5 2 2.7 3.5 3.5L8 7l2 2-1.5 1.5C4.5 10 1 6.5.5 2.5z" fill="#333"/></svg></span><span>Call Us<br>222.333.4444</span></div>
<div class="foot-item" style="left:694px;top:2330px"><span class="foot-icon"><svg width="12" height="9" viewBox="0 0 12 9"><rect width="12" height="9" rx="1" fill="#333"/><path d="M1 1l5 4 5-4" fill="none" stroke="#fff" stroke-width="1"/></svg></span><span>E mail Us<br>post@lappelund.no</span></div>

<div class="abs foot-h" style="left:958px">FOLLOW US</div>
<div class="foot-item" style="left:958px;top:2227px"><span class="foot-icon"></span><span>Like us on<br>FJORDBOOK</span></div>
<div class="foot-item" style="left:958px;top:2278px"><span class="foot-icon"></span><span>Follow us on<br>KVITRE</span></div>
<div class="foot-item" style="left:958px;top:2329px"><span class="foot-icon"></span><span>Follow us on<br>LINKNETT</span></div>

<div class="abs divider"></div>
<div class="abs copy">Copyright © 2021 All Rights Reserved</div>

</body>
</html>
```